Business Card Design Project - del varosi group

dear Sirs

we need business card design for our group ( DEL Varosi Group ) , i have got the Logo design of our group from pixel harbor in previous , so all need details relating to our group i think available with you, as well as the the chosen logo design

we hope to provide us with business card logo that to be appropaite and satisfactory to us .

thanks

note : logo design of our group is attached .
Updates

Reason: please extend the deadline of my project for additional 15 days because i didn't received appropriate design for our gruop yet . kindly beaware that i have received 77 design till now , supossed to send me 200-250 design at least . thanks

Target Market(s)

contents

name : Kerem EL Nadiri

position : Operation Manager

Industry/Entity Type

Business

Requirements
Must have

• person name

group logo
Nice to have
• logo color matching with back background

```html
<!DOCTYPE html>
<html lang="en">
<head>
<meta charset="utf-8">
<title>DEL Varosi Group – Business Card</title>
<link rel="stylesheet" href="https://fonts.googleapis.com/css2?family=Open+Sans:wght@400;600&display=swap">
<style>
  :root {
    --page-bg: #f3ead6;
    --page-edge: #e6d6b2;
    --gold-light: #e2b55a;
    --gold-mid: #d09c3c;
    --gold-dark: #b3802a;
    --navy: #1d4f92;
    --navy-deep: #163f78;
    --card-white: #ffffff;
    --card-grey: #ececec;
    --text-light: #ffffff;
    --text-name: #e6c77f;
    --text-dark: #1a2740;
  }
  * { box-sizing: border-box; margin: 0; padding: 0; }
  html, body { width: 1200px; height: 951px; overflow: hidden; }
  body {
    background: radial-gradient(ellipse at center, var(--page-bg) 55%, var(--page-edge) 100%);
    font-family: "Open Sans", Arial, sans-serif;
    position: relative;
  }
  .card {
    position: absolute;
    width: 540px;
    height: 310px;
    border-radius: 22px;
    overflow: hidden;
    box-shadow: 0 6px 18px rgba(80, 60, 20, 0.25);
  }
  /* Front */
  .card-front {
    left: 80px;
    top: 110px;
    background: linear-gradient(135deg, var(--gold-light) 0%, var(--gold-mid) 55%, var(--gold-dark) 100%);
  }
  .brand {
    position: absolute;
    left: 60px;
    top: 150px;
    display: flex;
    align-items: center;
    gap: 14px;
  }
  .brand-mark {
    width: 26px;
    height: 26px;
    background: var(--navy);
  }
  .brand-name {
    font-weight: 600;
    font-size: 40px;
    letter-spacing: 1px;
    color: var(--navy);
    text-transform: uppercase;
    line-height: 1;
  }
  /* Back */
  .card-back {
    left: 600px;
    top: 520px;
    background: linear-gradient(180deg, var(--card-white) 0%, var(--card-grey) 100%);
  }
  .info-band {
    position: absolute;
    left: 24px;
    right: 0;
    top: 70px;
    height: 190px;
    display: flex;
  }
  .person {
    width: 190px;
    background: var(--navy);
    background: linear-gradient(180deg, var(--navy) 0%, var(--navy-deep) 100%);
    padding: 52px 0 0 22px;
  }
  .person-name {
    color: var(--text-name);
    font-size: 19px;
    font-weight: 400;
    white-space: nowrap;
  }
  .person-role {
    color: var(--text-light);
    font-size: 15px;
    margin-top: 4px;
  }
  .contact {
    flex: 1;
    background: linear-gradient(135deg, var(--gold-light) 0%, var(--gold-mid) 60%, var(--gold-dark) 100%);
    position: relative;
    padding: 12px 0 0 50px;
  }
  .contact::before {
    content: "";
    position: absolute;
    left: 22px;
    top: 40px;
    bottom: 40px;
    width: 2px;
    background: rgba(255, 255, 255, 0.45);
  }
  .contact-list { list-style: none; }
  .contact-list li {
    display: flex;
    align-items: flex-start;
    gap: 9px;
    color: var(--text-dark);
    font-size: 14.5px;
    line-height: 19px;
  }
  .contact-list li + li { margin-top: 2px; }
  .contact-list .address { margin-bottom: 6px; }
  .contact-list svg { width: 14px; height: 14px; flex: none; margin-top: 2px; fill: var(--text-dark); }
</style>
</head>
<body>
  <section class="card card-front" aria-label="Card front">
    <div class="brand">
      <span class="brand-mark"></span>
      <span class="brand-name">DEL Varosi Group</span>
    </div>
  </section>

  <section class="card card-back" aria-label="Card back">
    <div class="info-band">
      <div class="person">
        <p class="person-name">Kerem EL Nadiri</p>
        <p class="person-role">Operation Manager</p>
      </div>
      <div class="contact">
        <ul class="contact-list">
          <li class="address">
            <svg viewBox="0 0 16 16"><path d="M8 1 1 7.5h2V15h4v-4h2v4h4V7.5h2z"/></svg>
            <span>4150 Corlane Blvd.<br>Suite 210-305<br>Hollis, TX 78114</span>
          </li>
          <li>
            <svg viewBox="0 0 16 16"><path d="M4.2 1.5 6.4 4 5 5.8a9 9 0 0 0 5.2 5.2L12 9.6l2.5 2.2-1.4 2.5C7.4 14 2 8.6 1.7 2.9z"/></svg>
            <span>555-014-2270</span>
          </li>
          <li>
            <svg viewBox="0 0 16 16"><path d="M4 1h8v4H4zM1 6h14v6h-3v3H4v-3H1zm4 5v3h6v-3z"/></svg>
            <span>555-014-2271</span>
          </li>
          <li>
            <svg viewBox="0 0 16 16"><path d="M1 3h14v10H1zm1.5 1.2L8 8.5l5.5-4.3z"/></svg>
            <span>info@delvarosigroup.com</span>
          </li>
          <li>
            <svg viewBox="0 0 16 16"><circle cx="8" cy="8" r="7"/></svg>
            <span>www.delvarosigroup.com</span>
          </li>
        </ul>
      </div>
    </div>
  </section>
</body>
</html>
```